Electric mountain bike tours nz

We are an Electric Mountain bike tour company in New Zealand. We will be offering bike rental and guided tours around the Nelson region in New Zealand. I want our website to represent both Mountain biking and New Zealand with the colours layout and features. We want tabs for the following:
-1 about us
-2 what we offer
-3 bookings/contact
Under the about us tab will be who we are as a a company. I want the ability to add videos to each of these tabs as we move foward with videos of the tracks we will be riding. I want the website to be editable so I can add and remove videos/photos myself. Also "our bikes" will be under this tab.
Under the what we offer tab will be
-1 bike rental and pricing
-2 guided tours and pricing
-3 recommended package deals.
I want to able to put the tracks under the guided tours tab and select beginner/ intermediate/advanced and have the tracks in each of the following to match the rider level. Also to be able to have a small video of the track would be great in this section.
Bookings and contact tab
(Further information for this tab to be updated soon)
Coded - Design and coding required
1 page
- Silver ferns, kiwi, mountains

```html
<!DOCTYPE html>
<html lang="en">
<head>
<meta charset="utf-8">
<title>Trailvolt – Electric Mountain Bike Tours</title>
<link href="https://fonts.googleapis.com/css2?family=Lato:ital,wght@0,400;0,700;0,900;1,700;1,900&family=Open+Sans:wght@400;600;700&display=swap" rel="stylesheet">
<style>
:root{
  --black:#0b0b0b;
  --white:#ffffff;
  --ink:#1d1d1d;
  --muted:#555555;
  --blue:#1f6fe0;
  --green:#1f9a2a;
  --green-deep:#157a1f;
  --orange:#f26a1b;
  --std-green:#2f9a3a;
  --ult-blue:#2346b3;
  --card-dark:#222222;
  --line:#3a3a3a;
  --footer:#d8d8d8;
  --star:#f2b21b;
  --fern:#e4e4e4;
  --fern-edge:#d6d6d6;
  --kiwi:#8a6a48;
  --kiwi-dark:#5e452e;
}
*{box-sizing:border-box;margin:0;padding:0}
html,body{width:1200px;height:3543px;overflow:hidden}
body{position:relative;background:var(--white);font-family:'Open Sans',sans-serif;color:var(--ink)}
.abs{position:absolute}

/* header */
.site-header{left:0;top:0;width:1200px;height:95px;background:var(--black);z-index:5}
.brand{left:189px;top:2px;width:156px;height:156px;border-radius:50%;background:var(--black);border:4px solid var(--white);display:flex;align-items:center;justify-content:center;z-index:6}
.brand-name{font-family:'Lato',sans-serif;font-weight:900;font-size:26px;color:var(--white);letter-spacing:1px}
.main-nav{top:46px;left:0;width:1200px;height:24px;z-index:6}
.main-nav a{position:absolute;top:0;font-family:'Lato',sans-serif;font-weight:700;font-size:13px;color:var(--white);text-decoration:none;white-space:nowrap;transform:translateX(-50%)}
.nav-pin{left:548px;top:16px;width:14px;height:14px;border-radius:50%;background:#8a7a5a;z-index:6}

/* hero */
.hero-photo{left:0;top:0;width:1200px;height:720px;background:linear-gradient(180deg,#1d4f9e 0%,#4d86cc 28%,#8fb4de 42%,#2b3a44 58%,#1a1f1c 80%,#0f120f 100%)}
.hero-title{left:0;top:262px;width:1200px;text-align:center;font-family:'Lato',sans-serif;font-weight:700;font-size:40px;line-height:44px;color:var(--white);text-transform:uppercase}
.btn{display:flex;align-items:center;justify-content:center;border-radius:22px;font-family:'Lato',sans-serif;font-weight:700;font-size:17px;color:var(--white);background:var(--blue);text-decoration:none}
.hero-btn{left:518px;top:363px;width:165px;height:40px}
.hero-dots{left:1073px;top:326px;width:12px}
.hero-dots span{display:block;width:11px;height:11px;border-radius:50%;background:var(--white);margin-bottom:9px}
.hero-dots span:first-child{background:transparent;border:2px solid var(--white)}
.tear{left:0;width:1200px}

/* placeholders */
.fern-ph{border-radius:18px;background:linear-gradient(150deg,var(--fern) 0%,#f1f1f1 100%);border:1px solid var(--fern-edge)}
.fern-left{left:48px;top:760px;width:230px;height:400px}
.fern-right{left:925px;top:965px;width:240px;height:195px}
.kiwi-ph{border-radius:14px;background:linear-gradient(180deg,var(--kiwi) 0%,var(--kiwi-dark) 100%);border:2px solid rgba(255,255,255,.7)}

/* about */
.section-icon{left:560px;width:80px;height:40px}
.section-title{left:0;width:1200px;text-align:center;font-family:'Lato',sans-serif;font-weight:700;font-size:34px;color:var(--ink);text-transform:uppercase}
.about-text{left:300px;top:820px;width:600px;text-align:center;font-size:12.5px;line-height:21px;color:var(--muted)}
.about-text p+p{margin-top:12px}
.about-btn{left:522px;top:999px;width:166px;height:42px}

/* video */
.video-band{left:0;top:1170px;width:1200px;height:490px;background:linear-gradient(120deg,#2fae34 0%,#1f9a2a 40%,#188a22 70%,#25a22d 100%)}
.video-icon{left:205px;top:1265px;width:90px;height:40px}
.video-title{left:205px;top:1306px;font-family:'Lato',sans-serif;font-weight:700;font-size:26px;color:var(--white);text-transform:uppercase}
.video-text{left:205px;top:1355px;width:330px;font-size:12.5px;line-height:24px;color:#e8f5e8}
.btn-outline{left:208px;top:1503px;width:170px;height:42px;border:2px solid var(--white);background:transparent;border-radius:22px}
.video-frame{left:561px;top:1265px;width:488px;height:302px}
.video-screen{left:574px;top:1277px;width:465px;height:280px;background:linear-gradient(135deg,#4a4a4a 0%,#2e2e2e 50%,#1b1b1b 100%)}
.play{left:764px;top:1368px;width:84px;height:84px}

/* packages */
.package-bg{left:0;top:1655px;width:1200px;height:780px;background:linear-gradient(180deg,#ffffff 0%,#eef3f8 18%,#c9d5e2 45%,#9fb1c4 65%,#e7edf3 100%)}
.kiwi-pack{left:150px;top:1788px;width:94px;height:108px}
.tabs{left:0;top:1811px;width:1200px;height:22px}
.tab{position:absolute;top:0;height:22px;padding:0 8px;display:flex;align-items:center;font-family:'Lato',sans-serif;font-weight:700;font-size:11px;color:var(--ink);transform:translateX(-50%);white-space:nowrap}
.tab.active{background:var(--black);color:var(--white)}
.plan{width:279px}
.plan-head{display:flex;align-items:center;justify-content:center;font-family:'Lato',sans-serif;font-weight:900;font-style:italic;font-size:22px;color:var(--white);text-transform:uppercase}
.plan-price{position:relative;display:flex;align-items:center;justify-content:center;color:var(--white);font-family:'Lato',sans-serif}
.plan-price .cur{font-size:20px;font-weight:700;align-self:flex-start;margin-top:30px}
.plan-price .amt{font-size:58px;font-weight:900;font-style:italic}
.plan-price .per{font-size:12px;margin-top:28px}
.plan-body{background:var(--card-dark);text-align:center;color:var(--white)}
.plan-body h3{font-family:'Lato',sans-serif;font-weight:700;font-style:italic;font-size:17px;text-transform:uppercase;padding:22px 0 18px}
.plan-body li{list-style:none;font-size:11.5px;height:43px;line-height:43px;border-top:1px solid var(--line)}
.plan-body .book{display:inline-flex;align-items:center;justify-content:center;width:103px;height:30px;border-radius:16px;background:var(--green-deep);font-family:'Lato',sans-serif;font-weight:900;font-size:12px;color:var(--white);margin-top:4px}
.starter{left:177px;top:1904px;z-index:2}
.starter .plan-head{height:34px;background:var(--orange)}
.starter .plan-price{height:117px;background:#f07a2e}
.starter .plan-body{height:355px}
.standard{left:456px;top:1873px;z-index:3}
.standard .plan-head{height:45px;background:var(--std-green)}
.standard .plan-price{height:137px;background:#34a545}
.standard .plan-body{height:383px}
.standard .plan-body h3{padding-top:24px}
.standard .book{margin-top:12px}
.ultimate{left:735px;top:1904px;z-index:2}
.ultimate .plan-head{height:34px;background:var(--ult-blue)}
.ultimate .plan-price{height:117px;background:#2c55c5}
.ultimate .plan-body{height:355px}

/* testimonials */
.testi-title{top:2493px}
.testi{top:2582px;width:255px}
.avatar{position:absolute;left:0;top:0;width:52px;height:52px;border-radius:50%;background:linear-gradient(160deg,#c9a58a,#6e4f3e)}
.avatar::after{content:"";position:absolute;left:34px;top:38px;width:14px;height:14px;border-radius:50%;background:var(--green)}
.testi-body{position:absolute;left:64px;top:0;width:190px}
.stars{color:var(--star);font-size:12px;letter-spacing:1px}
.quote{font-size:9.5px;line-height:15px;color:#666;font-style:italic;margin-top:6px}
.t-name{font-family:'Lato',sans-serif;font-weight:700;font-size:11px;margin-top:12px;color:var(--ink)}
.t-role{font-size:9.5px;color:#777;margin-top:6px}
.arrow{width:20px;height:20px;top:2672px}
.testi-dots{left:586px;top:2754px;display:flex;gap:5px}
.testi-dots span{width:8px;height:8px;border-radius:50%;border:1px solid #999}
.testi-dots span.on{background:var(--green);border-color:var(--green)}

/* booking */
.booking-photo{left:0;top:2830px;width:1200px;height:545px;background:linear-gradient(100deg,#0d0f0c 0%,#1a1f17 35%,#3d4a2c 60%,#6b5a3a 78%,#2a2a22 100%)}
.kiwi-book{left:1005px;top:2730px;width:150px;height:170px;z-index:2}
.bike-area{left:640px;top:3030px;width:260px;height:180px;border-radius:14px;background:linear-gradient(135deg,#e07a22 0%,#a9521c 100%);border:2px solid rgba(255,255,255,.35)}
.booking-title{left:217px;top:2990px;font-family:'Lato',sans-serif;font-weight:700;font-size:30px;color:var(--white);text-transform:uppercase}
.booking-lead{left:217px;top:3046px;width:370px;font-size:13.5px;line-height:21px;color:#e6e6e6}
.booking-text{left:217px;top:3105px;width:370px;font-size:12px;line-height:21px;color:#bcbcbc}
.booking-btn{left:217px;top:3218px;width:168px;height:42px}

/* footer */
.site-footer{left:0;top:3370px;width:1200px;height:173px;background:linear-gradient(180deg,#bfbfbf 0%,#d9d9d9 40%,#e6e6e6 100%)}
.footer-brand{left:198px;top:3405px;width:115px;height:115px;border-radius:50%;background:var(--footer);border:3px solid #444;display:flex;align-items:center;justify-content:center}
.footer-brand .brand-name{color:#333;font-size:19px}
.footer-nav a{position:absolute;top:3434px;font-family:'Lato',sans-serif;font-weight:700;font-size:13px;color:#2a2a2a;text-decoration:none;white-space:nowrap}
.copyright{left:350px;top:3470px;font-size:11px;color:#555}
.social{left:893px;top:3432px;display:flex;gap:8px}
.social span{width:26px;height:26px;border-radius:50%;background:#1b1b1b}
</style>
</head>
<body>

<!-- HERO -->
<div class="abs hero-photo" role="img" aria-label="Group of riders raising their arms beside electric mountain bikes at sunset above a lake"></div>
<svg class="abs tear" style="top:610px" width="1200" height="112" viewBox="0 0 1200 112" aria-hidden="true">
  <polygon fill="#ffffff" points="0,60 60,72 120,55 170,66 230,48 290,62 350,40 400,58 460,44 520,60 570,30 610,12 640,28 690,45 740,38 800,52 860,36 920,54 980,42 1040,58 1100,46 1160,62 1200,50 1200,112 0,112"/>
</svg>
<h1 class="abs hero-title">Electric Mountain<br>Bike Tours in New Zealand</h1>
<a class="abs btn hero-btn" href="#about">Click here</a>
<div class="abs hero-dots"><span></span><span></span><span></span><span></span></div>

<header class="abs site-header"></header>
<div class="abs brand"><span class="brand-name">TRAILVOLT</span></div>
<div class="abs nav-pin" aria-hidden="true"></div>
<nav class="abs main-nav">
  <a href="#" style="left:555px">HOME</a>
  <a href="#about" style="left:634px">ABOUT US</a>
  <a href="#offer" style="left:747px">WHAT WE OFFER</a>
  <a href="#booking" style="left:860px">BOOKINGS</a>
  <a href="#contact" style="left:962px">CONTACT US</a>
</nav>

<!-- ABOUT -->
<section id="about">
  <div class="abs fern-ph fern-left" role="img" aria-label="Large faint silver fern leaf decoration"></div>
  <div class="abs fern-ph fern-right" role="img" aria-label="Faint silver fern leaf decoration"></div>
  <svg class="abs section-icon" style="top:722px" viewBox="0 0 80 40" aria-hidden="true">
    <polyline points="8,34 30,10 42,22 52,12 72,34" fill="none" stroke="#2a86d8" stroke-width="4" stroke-linejoin="round"/>
  </svg>
  <h2 class="abs section-title" style="top:762px">About us</h2>
  <div class="abs about-text">
    <p>mi quis lacus mollis aliquam viscelerisque mi tortor at ipsum cligula augue bibendum accumsan vestibulum ut commodo a mi Morbi ornare gravida elit integer congue</p>
    <p>Aapsum dui aliquet felis at cursus magna nisi nec elit Praesent elementum elit at tellus nec ultricies sit amet porttitor mattis enim In massa libero interdum nec interdum vel blandit sed nulla In ullamcorper est eget tempor cursus neque mi consectetuer mi a ultricies massa est sed nisl Class aptent taciti sociosqu ad litora torquent per conubia nostra per incepto</p>
  </div>
  <a class="abs btn about-btn" href="#">Read More</a>
</section>

<!-- VIDEO -->
<section>
  <div class="abs video-band" role="img" aria-label="Green painted band with misty mountain forest"></div>
  <svg class="abs tear" style="top:1160px" width="1200" height="40" viewBox="0 0 1200 40" aria-hidden="true">
    <polygon fill="#ffffff" points="0,0 1200,0 1200,20 1140,26 1080,16 1010,28 950,18 880,30 820,20 760,26 700,14 640,24 580,18 520,30 460,20 400,28 340,16 280,26 220,18 160,30 100,20 40,26 0,18"/>
  </svg>
  <svg class="abs tear" style="top:1632px" width="1200" height="30" viewBox="0 0 1200 30" aria-hidden="true">
    <polygon fill="#ffffff" points="0,14 50,8 110,18 170,6 240,16 300,10 370,20 430,8 500,16 560,6 630,18 700,10 770,20 840,8 910,16 980,6 1050,18 1120,10 1200,16 1200,30 0,30"/>
  </svg>
  <svg class="abs video-icon" viewBox="0 0 90 40" aria-hidden="true">
    <polyline points="4,34 30,8 44,22 56,12 86,34" fill="none" stroke="#ffffff" stroke-width="4" stroke-linejoin="round"/>
  </svg>
  <h2 class="abs video-title">Watch our video</h2>
  <p class="abs video-text">penatibus et magnis dis parturient montes nascetur ridiculus mus In iaculis facilisis massa Etiam Suspendisse quam leo molestie sed luctus quis feugiat in pede Fusce tellus Sed metus augue convallis et vehicula ut pulvinar eu ante integer orci tellus</p>
  <a class="abs btn btn-outline" href="#">Click here</a>
  <svg class="abs video-frame" viewBox="0 0 488 302" aria-hidden="true">
    <polyline points="1,60 1,1 70,1" fill="none" stroke="#ffffff" stroke-width="2"/>
    <polyline points="418,301 487,301 487,240" fill="none" stroke="#ffffff" stroke-width="2"/>
  </svg>
  <div class="abs video-screen" role="img" aria-label="Video still of electric mountain bikes lined up in a workshop"></div>
  <svg class="abs play" viewBox="0 0 84 84" aria-hidden="true">
    <circle cx="42" cy="42" r="38" fill="rgba(0,0,0,.35)" stroke="#ffffff" stroke-width="4"/>
    <polygon points="33,26 60,42 33,58" fill="#ffffff"/>
  </svg>
</section>

<!-- PACKAGES -->
<section id="offer">
  <div class="abs package-bg" role="img" aria-label="Snow-capped mountain range under a pale sky"></div>
  <svg class="abs section-icon" style="top:1695px" viewBox="0 0 80 40" aria-hidden="true">
    <polyline points="6,34 32,8 44,20 54,12 74,34" fill="none" stroke="#777777" stroke-width="4" stroke-linejoin="round"/>
  </svg>
  <h2 class="abs section-title" style="top:1730px;font-size:26px">Our package</h2>
  <div class="abs kiwi-ph kiwi-pack" role="img" aria-label="Kiwi bird standing on the starter card"></div>
  <div class="abs tabs">
    <span class="tab" style="left:475px">BIKE RENTAL</span>
    <span class="tab" style="left:581px">GUIDED TOURS</span>
    <span class="tab active" style="left:697px">RECOMMENDED</span>
  </div>

  <div class="abs plan starter">
    <div class="plan-head">Starter</div>
    <div class="plan-price"><span class="cur">$</span><span class="amt">19</span><span class="per">/ MONTH</span></div>
    <div class="plan-body">
      <h3>Single place travel</h3>
      <ul><li>Lorem ipsum doloret</li><li>At vero eos et accusamus</li><li>Nam libero tempore coluta</li><li>Excepteur sint occaecat</li><li>On the other had ensunce</li></ul>
      <span class="book">BOOK NOW</span>
    </div>
  </div>
  <div class="abs plan standard">
    <div class="plan-head">Standard</div>
    <div class="plan-price"><span class="cur">$</span><span class="amt">39</span><span class="per">/ MONTH</span></div>
    <div class="plan-body">
      <h3>Three place travel</h3>
      <ul><li>Nam libero tempore coluta</li><li>On the other had ensunce</li><li>Lorem ipsum doloret</li><li>At vero eos et accusamus</li><li>Excepteur sint occaecat</li></ul>
      <span class="book">BOOK NOW</span>
    </div>
  </div>
  <div class="abs plan ultimate">
    <div class="plan-head">Ultimate</div>
    <div class="plan-price"><span class="cur">$</span><span class="amt">59</span><span class="per">/ MONTH</span></div>
    <div class="plan-body">
      <h3>Five place travel</h3>
      <ul><li>Excepteur sint occaecat</li><li>Nam libero tempore coluta</li><li>At vero eos et accusamus</li><li>On the other had ensunce</li><li>Lorem ipsum doloret</li></ul>
      <span class="book">BOOK NOW</span>
    </div>
  </div>
</section>

<!-- TESTIMONIALS -->
<section>
  <h2 class="abs section-title testi-title" style="font-size:27px">Testimonials</h2>
  <svg class="abs arrow" style="left:116px" viewBox="0 0 20 20" aria-hidden="true"><polyline points="13,3 6,10 13,17" fill="none" stroke="#444" stroke-width="2"/></svg>
  <svg class="abs arrow" style="left:1070px" viewBox="0 0 20 20" aria-hidden="true"><polyline points="7,3 14,10 7,17" fill="none" stroke="#444" stroke-width="2"/></svg>

  <article class="abs testi" style="left:187px">
    <div class="avatar" role="img" aria-label="Portrait of the reviewer"></div>
    <div class="testi-body">
      <div class="stars">★★★★★</div>
      <p class="quote">“ At vero eos et accusamus et iustodio dignissimos ducimus qui blanditiipraesent ium voluptatum deleniti atque corrupti quos dolores quas molestias ”</p>
      <div class="t-name">MIRA SOLANO</div>
      <div class="t-role">Creative Manager, NZ</div>
    </div>
  </article>
  <article class="abs testi" style="left:472px">
    <div class="avatar" role="img" aria-label="Portrait of the reviewer"></div>
    <div class="testi-body">
      <div class="stars">★★★★★</div>
      <p class="quote">“ At vero eos et accusamus et iustodio dignissimos ducimus qui blanditiipraesent ium voluptatum deleniti atque corrupti quos dolores quas molestias ”</p>
      <div class="t-name">TOMAS KERRIGAN</div>
      <div class="t-role">Events Manager, NZ</div>
    </div>
  </article>
  <article class="abs testi" style="left:767px">
    <div class="avatar" role="img" aria-label="Portrait of the reviewer"></div>
    <div class="testi-body">
      <div class="stars">★★★★★</div>
      <p class="quote">“ At vero eos et accusamus et iustodio dignissimos ducimus qui blanditiipraesent ium voluptatum deleniti atque corrupti quos dolores quas molestias ”</p>
      <div class="t-name">IVAN ROWELL</div>
      <div class="t-role">Sports Manager, NZ</div>
    </div>
  </article>
  <div class="abs testi-dots"><span></span><span class="on"></span><span></span></div>
</section>

<!-- BOOKING -->
<section id="booking">
  <div class="abs booking-photo" role="img" aria-label="Dark forest trail with tree trunks and an orange mountain bike"></div>
  <svg class="abs tear" style="top:2815px" width="1200" height="60" viewBox="0 0 1200 60" aria-hidden="true">
    <polygon fill="#ffffff" points="0,0 1200,0 1200,40 1150,30 1100,44 1040,24 980,38 920,22 860,36 800,26 740,40 680,28 620,42 560,30 500,44 440,26 380,40 320,28 260,42 200,30 140,44 80,30 0,40"/>
  </svg>
  <div class="abs bike-area" role="img" aria-label="Orange full-suspension mountain bike on the trail"></div>
  <div class="abs kiwi-ph kiwi-book" role="img" aria-label="Kiwi bird perched above the booking section"></div>
  <h2 class="abs booking-title">Our booking</h2>
  <p class="abs booking-lead">Arnare gravida elit integer congue augue et malesuada iaculis ipsum dui aliquet felis at cursus ma</p>
  <p class="abs booking-text">libero interdum nec interdum vel blandit sed nulla In ullamcorper est eget tempor cursus neque mi consectetuer mi a ultricies massa est sed nisl Class aptent taciti sociosqu ad litora torquent per conubia nostra per</p>
  <a class="abs btn booking-btn" href="#">Read More</a>
</section>

<!-- FOOTER -->
<footer id="contact">
  <div class="abs site-footer" role="img" aria-label="Pale grey mountain silhouettes"></div>
  <div class="abs footer-brand"><span class="brand-name">TRAILVOLT</span></div>
  <nav class="footer-nav">
    <a href="#" style="left:350px">HOME</a>
    <a href="#about" style="left:420px">ABOUT US</a>
    <a href="#offer" style="left:514px">WHAT WE OFFER</a>
    <a href="#booking" style="left:652px">BOOKINGS</a>
    <a href="#contact" style="left:752px">CONTACT US</a>
  </nav>
  <p class="abs copyright">© 2018 Company Name  All right reserved</p>
  <div class="abs social" aria-label="Social links"><span></span><span></span><span></span><span></span></div>
</footer>

</body>
</html>
```